Geschäftspapiere für junges Unternehmen aus dem Garten- und Landschaftsbau
Zielgruppe
Wir sind ein junges Unternehmen im Bereich Garten und Landschaftsbau, wir beschäftigen uns mit pflege von Gärten sowie die Neu und Umgestaltung von Gärten. Unsere Zielguppe ist der Privatgarten und zum kleinen Teil auch Gewerbekunden.
Aufgabenstellung
Es sollen die Elemente der Bilder beinhalten, der Nachname und die Branchenbezeichnung enthalten sein. Die Fußzeile des Geschäftpapiers sind vorgesehen und die Daten werden erst angegeben wenn der bestimmte Entwurf mir zusagt.

```html
<!DOCTYPE html>
<html lang="de">
<head>
<meta charset="utf-8">
<title>Briefbogen Torem Vasch – Garten und Landschaftsbau</title>
<link rel="stylesheet" href="https://fonts.googleapis.com/css2?family=Open+Sans:ital,wght@0,400;0,600;1,600&display=swap">
<style>
  :root {
    --backdrop: #e9e8e5;
    --paper: #ffffff;
    --forest-dark: #0f5a2c;
    --leaf-green: #4cb14a;
    --ring-green: #6b8f68;
    --ink: #1e1e1e;
    --header-light: #f2f5f2;
  }
  * { margin: 0; padding: 0; box-sizing: border-box; }
  html, body {
    width: 966px; height: 1200px; overflow: hidden;
    background: var(--backdrop);
    font-family: "Open Sans", Arial, sans-serif;
    color: var(--ink);
  }
  .letterhead {
    position: absolute; left: 58px; top: 0;
    width: 850px; height: 1200px;
    background: var(--paper);
  }
  .masthead {
    position: absolute; left: 0; top: 0; width: 850px; height: 196px;
    overflow: hidden;
  }
  .masthead-photo {
    position: absolute; inset: 0;
    background:
      linear-gradient(90deg, rgba(8,20,14,.55) 0%, rgba(8,20,14,0) 30%, rgba(8,20,14,0) 70%, rgba(5,14,10,.8) 100%),
      linear-gradient(180deg, #4f6b60 0%, #3a5548 45%, #2a3f30 75%, #1f3322 100%);
  }
  .trade-title {
    position: absolute; left: 108px; top: 34px;
    color: var(--header-light);
    font-style: italic; font-weight: 600; font-size: 27px; line-height: 37px;
    text-shadow: 0 1px 3px rgba(0,0,0,.45);
  }
  .contact-item { position: absolute; top: 135px; display: flex; align-items: flex-start; }
  .contact-icon {
    width: 29px; height: 29px; border-radius: 6px;
    background: var(--leaf-green);
    display: flex; align-items: center; justify-content: center;
  }
  .contact-text {
    color: var(--header-light); font-size: 11.5px; line-height: 16px; font-weight: 600;
    white-space: nowrap;
  }
  .contact-address { left: 106px; }
  .contact-address .contact-text { margin-left: 17px; margin-top: 2px; }
  .contact-phone { left: 277px; }
  .contact-phone .contact-text { margin-left: 16px; margin-top: -3px; }
  .contact-web { left: 452px; }
  .contact-web .contact-text { margin-left: 19px; margin-top: -1px; }
  .brand-mark {
    position: absolute; left: 668px; top: 21px; width: 136px; height: 136px;
    border-radius: 50%; border: 8px solid var(--ring-green);
    display: flex; align-items: center; justify-content: center;
  }
  .brand-name {
    color: var(--header-light); font-weight: 600; font-size: 15px;
  }
  .sender-line {
    position: absolute; left: 112px; top: 213px;
    font-size: 10.5px; white-space: nowrap;
  }
  .sender-name { color: var(--leaf-green); font-weight: 600; }
  .footer-rule {
    position: absolute; left: 68px; top: 1096px; width: 602px; height: 3px;
    background: var(--forest-dark);
  }
  .footer-column {
    position: absolute; top: 1128px; font-size: 13px; line-height: 18px; white-space: nowrap;
  }
  .footer-owner { left: 68px; }
  .footer-bank { left: 278px; }
  .footer-account { left: 450px; }
  .footer-divider {
    position: absolute; top: 1127px; width: 2px; height: 37px; background: var(--leaf-green);
  }
  .footer-divider.first { left: 259px; }
  .footer-divider.second { left: 430px; }
  .footer-brand {
    position: absolute; left: 700px; top: 1150px; display: flex; align-items: center; gap: 8px;
    color: var(--forest-dark); font-weight: 600; font-size: 15px;
  }
  .footer-brand-dot { width: 14px; height: 14px; border-radius: 50%; background: var(--leaf-green); }
  .base-band {
    position: absolute; left: 0; bottom: 0; width: 850px; height: 7px;
    background: var(--forest-dark);
  }
</style>
</head>
<body>
  <main class="letterhead">
    <header class="masthead">
      <div class="masthead-photo" role="img" aria-label="Nebliger Nadelwald mit hohen Baumstämmen"></div>
      <h1 class="trade-title">Garten und Landschaftsbau<br>Weihnachtsbäume Baumfällung</h1>

      <div class="contact-item contact-address">
        <span class="contact-icon">
          <svg width="17" height="17" viewBox="0 0 24 24" aria-hidden="true"><path d="M12 3 2 12h3v8h5v-5h4v5h5v-8h3z" fill="#fff"/></svg>
        </span>
        <span class="contact-text">Lindenhofweg 12<br>55597 Eschental</span>
      </div>
      <div class="contact-item contact-phone">
        <span class="contact-icon">
          <svg width="16" height="16" viewBox="0 0 24 24" aria-hidden="true"><path d="M6.6 10.8a15 15 0 0 0 6.6 6.6l2.2-2.2c.3-.3.7-.4 1-.2 1.1.4 2.3.6 3.6.6.6 0 1 .4 1 1V20c0 .6-.4 1-1 1A17 17 0 0 1 3 4c0-.6.4-1 1-1h3.5c.6 0 1 .4 1 1 0 1.3.2 2.5.6 3.6.1.3 0 .7-.2 1z" fill="#fff"/></svg>
        </span>
        <span class="contact-text">T + 49 671 480 2210<br>M 0152 38 74 61 09</span>
      </div>
      <div class="contact-item contact-web">
        <span class="contact-icon">
          <svg width="17" height="17" viewBox="0 0 24 24" aria-hidden="true"><circle cx="12" cy="12" r="9" fill="none" stroke="#fff" stroke-width="2"/><path d="M3 12h18M12 3c3 3 3 15 0 18M12 3c-3 3-3 15 0 18" fill="none" stroke="#fff" stroke-width="1.6"/></svg>
        </span>
        <span class="contact-text">torem.vasch@gartenpost.de<br>www.torem-vasch.de</span>
      </div>

      <div class="brand-mark"><span class="brand-name">Toremvasch</span></div>
    </header>

    <p class="sender-line"><span class="sender-name">Torem Vasch I</span> Lindenhofweg 12, 55597 Eschental</p>

    <footer>
      <div class="footer-rule"></div>
      <div class="footer-column footer-owner">Torem Vasch<br>Steurliche ID: DE 204815963</div>
      <div class="footer-divider first"></div>
      <div class="footer-column footer-bank">Bankwerbindung:<br>Feldbank Eschental</div>
      <div class="footer-divider second"></div>
      <div class="footer-column footer-account">BIC: FELDDEX1ESC<br>IBAN: DE12 5006 0400 0012 3456 78</div>
      <div class="footer-brand"><span class="footer-brand-dot"></span>Toremvasch</div>
      <div class="base-band"></div>
    </footer>
  </main>
</body>
</html>
```